Clinic for cellulit and fat removal

Name of clinic :
Lirava
- Body & Health (this has to be written on the site.)
I need CMS for me to be able to make changes myself.
A webpage for woman searching for a solution to remove fat and cellulit.
The owner is a brazilian woman in Denmark, and want her sense of aestetic shines thru the website.
There needs to be a slide show on the landing page showing big sliding pictures, of the clinic and and the treatments.
The Cryolipolysis, is a treatment freezing fat and cellulit, and this treatment will be the Attraction of the clinic.
Needs These pages in a horisontal fasion. (written in Danish)
Lirava
Behandlinger
- Cryolipolysis
- Trimflox
- Lymfemassage
- Korathelix
- Amberline Tide
Produkter
Priser
Kontakt
Clinic
Coded - Design and coding required
5+ page

```html
<!DOCTYPE html>
<html lang="en">
<head>
<meta charset="utf-8">
<title>Lirava – Body &amp; Health</title>
<link rel="stylesheet" href="https://fonts.googleapis.com/css2?family=Lato:wght@300;400;700;900&display=swap">
<style>
:root{
  --blue:#1ea6ec;
  --blue-dark:#1580c4;
  --ink:#3a3a3a;
  --text:#444;
  --dark:#333333;
  --card-label:#3b3b3b;
  --white:#fff;
  --grey:#d9d9d9;
}
*{box-sizing:border-box;margin:0;padding:0}
html,body{width:1200px;height:2889px;overflow:hidden;background:var(--white)}
body{position:relative;font-family:'Lato',sans-serif;color:var(--text)}
.abs{position:absolute}

/* top bar */
.topbar{left:0;top:0;width:1200px;height:67px;background:var(--blue);z-index:3}
.lang{left:87px;top:15px;width:134px;height:37px;border:1px solid rgba(255,255,255,.7);color:#fff;font-size:14px;padding:9px 14px;display:flex;justify-content:space-between;align-items:center}
.lang svg{width:10px;height:6px}
.phone-pill{left:835px;top:15px;width:130px;height:37px;border:1px solid rgba(255,255,255,.7);color:#fff;font-size:15px;display:flex;align-items:center;justify-content:center;gap:6px}
.social-pill{left:976px;top:15px;width:138px;height:37px;border:1px solid rgba(255,255,255,.7);display:flex;align-items:center;justify-content:center;gap:9px}
.dot{width:12px;height:12px;border-radius:50%;background:#fff}

/* hero */
.hero{left:0;top:0;width:1200px;height:703px;background:linear-gradient(100deg,#c8b2a6 0%,#9b8c86 30%,#8a8e9c 55%,#6f7591 75%,#8a86a8 100%);overflow:hidden}
.hero-shade{left:0;top:0;width:1200px;height:703px;background:rgba(40,40,50,.25)}
.nav{left:85px;top:67px;width:1030px;height:82px;border-bottom:1px solid rgba(255,255,255,.7);z-index:2}
.logo{left:0;top:22px;color:#fff;font-size:31px;font-weight:900;letter-spacing:.5px}
.menu{left:300px;top:32px;display:flex;gap:40px;color:#fff;font-size:15px}
.book{left:853px;top:21px;width:177px;height:37px;background:var(--blue);color:#fff;font-size:14px;display:flex;align-items:center;justify-content:center;border-radius:2px}
.hero-title{left:0;top:242px;width:1200px;text-align:center;color:#fff;font-size:58px;font-weight:700;z-index:2}
.hero-copy{left:250px;top:318px;width:700px;text-align:center;color:#fff;font-size:13.5px;line-height:21px;z-index:2}
.hero-btn{left:528px;top:400px;width:144px;height:47px;background:var(--blue-dark);color:#fff;font-size:14px;display:flex;align-items:center;justify-content:center;z-index:2}
.arrow{top:332px;width:22px;height:36px;z-index:2}
.hero-wave{left:0;top:540px;width:1200px;height:165px;z-index:2}

/* section headings */
.heading{left:0;width:1200px;text-align:center;color:var(--ink);font-size:42px;font-weight:400}
.rule{height:5px;width:120px;background:var(--blue)}

/* treatments */
.card{top:890px;width:250px;height:293px}
.card .photo{width:250px;height:241px}
.card .label{height:52px;background:var(--card-label);color:#fff;font-size:17px;display:flex;align-items:center;justify-content:center;letter-spacing:.5px}
.card.active .label{background:var(--blue)}
.pager{width:91px;height:39px;background:var(--grey);border:1px solid #c6c6c6;display:flex;align-items:center;justify-content:center;gap:5px}
.pager span{width:11px;height:11px;border-radius:50%;background:#9ad1f2}
.pager span.on{background:var(--blue)}

/* about */
.about{left:0;top:1356px;width:1200px;height:537px;background:radial-gradient(ellipse at 50% 40%,#ececec 0%,#d8d8d8 50%,#c4c4c6 100%)}
.about-copy{left:245px;top:1521px;width:710px;text-align:center;font-size:13px;line-height:21px;color:#333}
.about-copy p+p{margin-top:20px}
.about-btn{left:535px;top:1776px;width:130px;height:46px;background:var(--blue);color:#fff;font-size:13px;display:flex;align-items:center;justify-content:center;box-shadow:2px 3px 5px rgba(0,0,0,.3)}

/* stories */
.stories-title{left:87px;top:1963px;color:var(--ink);font-size:42px;font-weight:400}
.stories-copy{left:85px;top:2076px;width:510px;font-size:16.5px;line-height:28px;color:#444}
.see-more{left:87px;top:2211px;width:179px;height:58px;background:var(--blue);color:#fff;font-size:22px;display:flex;align-items:center;justify-content:center}
.polaroid{background:#fff;padding:14px 14px 40px;box-shadow:0 3px 10px rgba(0,0,0,.35)}
.polaroid .photo{width:100%;height:100%;background:linear-gradient(180deg,#e4e4e4,#cfcfd2)}

/* footer */
.footer-wave{left:0;top:2385px;width:1200px;height:130px}
.footer{left:0;top:2505px;width:1200px;height:384px;background:var(--dark);color:#fff}
.f-logo{left:85px;top:2595px;font-size:54px;font-weight:700;color:#fff}
.f-copy{left:85px;top:2678px;font-size:9px;color:#fff}
.f-head{top:2559px;font-size:17px;font-weight:700;color:#fff}
.f-line{left:391px;display:flex;gap:22px;font-size:11.5px;line-height:18px;color:#fff}
.f-line svg{width:12px;height:12px;flex:none;margin-top:3px}
.f-social{left:391px;top:2722px;display:flex;gap:10px}
.f-social span{width:17px;height:17px;background:#fff;border-radius:50%}
.field{left:672px;width:237px;border:1px solid #666;font-size:9px;color:#bbb;padding:8px 12px}
.send{left:672px;top:2779px;width:83px;height:33px;background:var(--blue);color:#fff;font-size:12px;display:flex;align-items:center;justify-content:center}
.sitemap{left:978px;top:2597px;font-size:11px;line-height:19px;color:#fff;list-style:none}
</style>
</head>
<body>

<!-- hero -->
<section class="abs hero">
  <div class="abs" role="img" aria-label="Slide photo: a woman relaxing on a treatment bed while a therapist in blue gloves applies a cryolipolysis device" style="left:0;top:0;width:1200px;height:703px"></div>
  <div class="abs hero-shade"></div>
</section>

<header class="abs topbar">
  <div class="abs lang">ENGLISH
    <svg viewBox="0 0 10 6"><path d="M0 0h10L5 6z" fill="#fff"/></svg>
  </div>
  <div class="abs phone-pill">
    <svg width="12" height="12" viewBox="0 0 24 24"><path fill="#fff" d="M6.6 10.8a15 15 0 0 0 6.6 6.6l2.2-2.2a1 1 0 0 1 1-.25 11.4 11.4 0 0 0 3.6.6 1 1 0 0 1 1 1V20a1 1 0 0 1-1 1A17 17 0 0 1 3 4a1 1 0 0 1 1-1h3.5a1 1 0 0 1 1 1c0 1.25.2 2.45.6 3.6a1 1 0 0 1-.25 1z"/></svg>
    555-210-4478
  </div>
  <div class="abs social-pill">
    <span class="dot"></span><span class="dot"></span><span class="dot"></span><span class="dot"></span><span class="dot"></span>
  </div>
</header>

<nav class="abs nav">
  <div class="abs logo">LIRAVA</div>
  <div class="abs menu"><span>LIRAVA</span><span>BEHANDLINGER</span><span>PRODUKTER</span><span>PRISER</span><span>KONTAKT</span></div>
  <div class="abs book">BOOK APPOINTMENT</div>
</nav>

<h1 class="abs hero-title">BODY &amp; HEALTH</h1>
<p class="abs hero-copy">At vero eos et iusto odio dignissimos ducimus qui blanditiis praesentium voluptatum deleniti atque corrupti quos dolores et quas molestias excepturi sint occaecati cupiditate non provident, similique sunt in culpa qui officia deserunt mollitia animi, id est laborum</p>
<div class="abs hero-btn">READ MORE &gt;</div>

<svg class="abs arrow" style="left:30px" viewBox="0 0 22 36"><path d="M18 3 4 18l14 15" fill="none" stroke="#fff" stroke-width="4"/></svg>
<svg class="abs arrow" style="left:1146px" viewBox="0 0 22 36"><path d="M4 3l14 15L4 33" fill="none" stroke="#fff" stroke-width="4"/></svg>

<svg class="abs hero-wave" viewBox="0 0 1200 165" preserveAspectRatio="none">
  <path d="M0 70C150 20 300 10 420 30C620 70 760 150 1000 130C1100 120 1160 95 1200 80V165H0Z" fill="var(--blue)"/>
  <path d="M0 72C150 25 300 20 420 40C600 75 700 160 950 160C1080 160 1150 145 1200 140V165H0Z" fill="#fff"/>
</svg>

<!-- treatments -->
<h2 class="abs heading" style="top:786px">BEHANDLINGER</h2>
<div class="abs rule" style="left:540px;top:851px"></div>

<div class="abs card" style="left:87px">
  <div class="photo" role="img" aria-label="Photo of a cryolipolysis treatment with a client lying on a bed" style="background:linear-gradient(135deg,#eae4df,#c9c2c0)"></div>
  <div class="label">CRYOLIPOLYSIS</div>
</div>
<div class="abs card" style="left:347px">
  <div class="photo" role="img" aria-label="Photo of a slim waist and hips with dotted contour marks" style="background:linear-gradient(135deg,#efefef,#d8b8a2)"></div>
  <div class="label">TRIMFLOX</div>
</div>
<div class="abs card active" style="left:605px">
  <div class="photo" role="img" aria-label="Photo of a lymphatic massage device used on a client's leg" style="background:linear-gradient(135deg,#d9b49a,#b07b5c)"></div>
  <div class="label">LYMFEMASSAGE</div>
</div>
<div class="abs card" style="left:863px">
  <div class="photo" role="img" aria-label="Photo of hands massaging a foot" style="background:linear-gradient(135deg,#e3c4b4,#c59580)"></div>
  <div class="label">KORATHELIX</div>
</div>

<div class="abs pager" style="left:555px;top:1219px"><span></span><span class="on"></span><span></span></div>

<!-- about -->
<section class="abs about" role="img" aria-label="Soft blurred photo of the clinic interior as background"></section>
<h2 class="abs heading" style="top:1412px">ABOUT LIRAVA</h2>
<div class="abs rule" style="left:546px;top:1477px"></div>
<div class="abs about-copy">
  <p>At vero eos et accusamus et iusto odio dignissimos ducimus qui blanditiis praesentium voluptatum deleniti atque corrupti quos dolores et quas molestias excepturi sint occaecati cupiditate non provident, similique sunt in culpa qui officia deserunt mollitia animi, id est laborum et dolorum fuga.</p>
  <p>Et harum quidem rerum facilis est et expedita distinctio. Nam libero tempore, cum soluta nobis est eligendi optio cumque nihil impedit quo minus id quod maxime placeat facere possimus, omnis voluptas assumenda est, omnis dolor repellendus. Temporibus autem quibusdam et aut officiis debitis aut rerum necessitatibus saepe eveniet ut et voluptates repudiandae sint et molestiae non recusandae. Itaque earum rerum hic tenetur a sapiente delectus, ut aut reiciendis voluptatibus maiores alias consequatur aut perferendis doloribus asperiores repellat</p>
</div>
<div class="abs about-btn">Read More &gt;</div>

<!-- stories -->
<h2 class="abs stories-title">REAL PEOPLE, REAL STORIES</h2>
<div class="abs rule" style="left:87px;top:2027px"></div>
<p class="abs stories-copy">At vero eos et accusamus et iusto odio dignissimos ducimus qui blanditiis praesentium voluptatum deleniti atque corrupti quos dolores et quas molestias excepturi sint occaecati cupiditate non provident,</p>
<div class="abs see-more">SEE MORE</div>

<div class="abs polaroid" style="left:880px;top:2015px;width:230px;height:250px;transform:rotate(5deg)">
  <div class="photo" role="img" aria-label="After photo of a client in a white shirt and jeans"></div>
</div>
<div class="abs polaroid" style="left:670px;top:2058px;width:235px;height:245px;transform:rotate(-3deg)">
  <div class="photo" role="img" aria-label="Before photo of a client in a white shirt and jeans"></div>
</div>
<div class="abs pager" style="left:847px;top:2336px"><span></span><span class="on"></span><span></span></div>

<!-- footer -->
<svg class="abs footer-wave" viewBox="0 0 1200 130" preserveAspectRatio="none">
  <path d="M0 30C150 -5 350 5 520 60C700 115 900 100 1200 20V130H0Z" fill="var(--blue)"/>
  <path d="M0 60C150 20 350 30 520 80C700 130 900 120 1200 45V130H0Z" fill="var(--dark)"/>
</svg>
<footer class="abs footer"></footer>

<div class="abs f-logo">LIRAVA</div>
<div class="abs f-copy">© Copyright 2017 Lirava | All Rights Reserved.</div>

<div class="abs f-head" style="left:391px">CONTACT US</div>
<div class="abs f-line" style="top:2605px">
  <svg viewBox="0 0 24 24"><path fill="#fff" d="M12 2a7 7 0 0 0-7 7c0 5 7 13 7 13s7-8 7-13a7 7 0 0 0-7-7zm0 9.5A2.5 2.5 0 1 1 12 6.5a2.5 2.5 0 0 1 0 5z"/></svg>
  <span>48 Solvang Allé, Nordby<br>Sjælland, 4520.</span>
</div>
<div class="abs f-line" style="top:2650px">
  <svg viewBox="0 0 24 24"><path fill="#fff" d="M6.6 10.8a15 15 0 0 0 6.6 6.6l2.2-2.2a1 1 0 0 1 1-.25 11.4 11.4 0 0 0 3.6.6 1 1 0 0 1 1 1V20a1 1 0 0 1-1 1A17 17 0 0 1 3 4a1 1 0 0 1 1-1h3.5a1 1 0 0 1 1 1c0 1.25.2 2.45.6 3.6a1 1 0 0 1-.25 1z"/></svg>
  <span>555-210-4478</span>
</div>
<div class="abs f-line" style="top:2678px">
  <svg viewBox="0 0 24 24"><path fill="#fff" d="M2 5h20v14H2zm2 2v.5l8 5 8-5V7z"/></svg>
  <span>hello@lirava-klinik.dk</span>
</div>
<div class="abs f-social"><span></span><span></span><span></span><span></span></div>

<div class="abs f-head" style="left:672px">ENQUIRE NOW</div>
<div class="abs field" style="top:2600px;height:39px">Name</div>
<div class="abs field" style="top:2650px;height:39px">Email</div>
<div class="abs field" style="top:2702px;height:62px">Message</div>
<div class="abs send">SEND</div>

<div class="abs f-head" style="left:978px">SITEMAP</div>
<ul class="abs sitemap">
  <li>&gt; Lirava</li>
  <li>&gt; Behandlinger</li>
  <li>&gt; Produkter</li>
  <li>&gt; Priser</li>
  <li>&gt; Kontakt</li>
</ul>

</body>
</html>
```